Garlic Farm for Farm Sales/Restaurant sales

Need a professional, but appealing to agriculture world. We are selling 27 kinds of Organic Garlic from a farm in Simla,CO. I have uploaded logo and business information-we are going to need a template, because I will need to use it for four separate people.
-We are trying to appeal to Farm to table restaurants
-As well as growers/farmers

Target Market(s)

Agriculture Sales/Restaurants-Organic

Industry/Entity Type

Agriculture

Contact Information for Business Card

Want it to look more unique then your average kelto stock card- I want it to look amazing

Font styles to use
Sans Serif

Colors
0455a3
ec1f27
fbed22
ffffff

Requirements
Must have
• Just be creative
Nice to have
• Colorful
Should not have
• plain

```html
<!DOCTYPE html>
<html lang="en">
<head>
<meta charset="utf-8">
<title>Summit Ridge Gourmet Garlic — Business Cards</title>
<link rel="stylesheet" href="https://fonts.googleapis.com/css2?family=Arimo:wght@400;700&family=Source+Sans+3:wght@400;600;700&display=swap">
<style>
  :root {
    --bg: #8f857c;
    --navy: #1f3170;
    --navy-edge: #13285e;
    --red: #d71f2e;
    --yellow: #f5d400;
    --cream: #f3e7a2;
    --white: #ffffff;
    --ink: #111111;
  }
  * { margin: 0; padding: 0; box-sizing: border-box; }
  html, body {
    width: 1200px; height: 864px; overflow: hidden;
    background: var(--bg);
  }
  .sheet {
    width: 1200px; height: 864px;
    display: flex; align-items: center; justify-content: center; gap: 40px;
  }
  .card {
    width: 525px; height: 300px; position: relative; overflow: hidden;
    background: var(--white);
  }

  /* Front card */
  .card-front {
    border: 6px solid var(--navy-edge);
    display: flex; flex-direction: column; align-items: center;
    padding-top: 42px;
    font-family: "Source Sans 3", sans-serif;
    color: var(--ink);
  }
  .brand-front {
    display: flex; align-items: center; gap: 14px;
  }
  .brand-dot {
    width: 64px; height: 64px; border-radius: 50%; background: var(--red);
  }
  .brand-front .brand-name {
    font-family: "Source Sans 3", sans-serif;
    font-weight: 700; font-size: 30px; color: var(--navy);
    line-height: 1.05;
  }
  .company {
    margin-top: 30px; text-align: center;
    font-size: 17px; font-weight: 600; line-height: 1.3;
  }
  .person {
    margin-top: 16px; font-size: 18px; font-weight: 700;
  }

  /* Back card */
  .card-back {
    font-family: "Arimo", sans-serif;
  }
  .back-top {
    height: 132px; background: var(--white);
    display: flex; align-items: center; justify-content: center; gap: 16px;
  }
  .brand-square {
    width: 46px; height: 46px; background: var(--navy);
  }
  .brand-back {
    font-family: "Arimo", sans-serif;
    font-weight: 400; font-size: 30px; color: var(--navy);
    letter-spacing: 2px; text-transform: uppercase; line-height: 1.1;
  }
  .back-bottom {
    position: absolute; left: 0; right: 0; top: 132px; bottom: 0;
    background: var(--navy);
    display: flex; flex-direction: column; align-items: center;
    padding-top: 26px;
    color: var(--cream); font-size: 17px; line-height: 1.45; text-align: center;
  }
  .origin { margin-bottom: 4px; }
</style>
</head>
<body>
  <main class="sheet">
    <section class="card card-front" aria-label="Business card front">
      <div class="brand-front">
        <span class="brand-dot" aria-hidden="true"></span>
        <span class="brand-name">Summit Ridge<br>Gourmet Garlic</span>
      </div>
      <p class="company">Valtrimo™ Tanager Farms<br>Quality Growers LLC</p>
      <p class="person">Dario Menth-COO</p>
    </section>

    <section class="card card-back" aria-label="Business card back">
      <div class="back-top">
        <span class="brand-square" aria-hidden="true"></span>
        <span class="brand-back">Summit Ridge<br>Gourmet Garlic</span>
      </div>
      <div class="back-bottom">
        <p class="origin">A product of the USA, Harlow Falls, NY</p>
        <p class="contact">For comments, suggestion, or ordering please<br>contact us at:<br>valtrimo22@mailbox.com</p>
      </div>
    </section>
  </main>
</body>
</html>
```